RevelHubQZ Business Cards

Front
Has logo with a design. Website address (www.revelhubqz-example.net)
Has slogan (discover the nightlife)
Has phone number (5182297734)
Should be bold and stands out.

Back
Has details about what we offer.

Events
Search upcoming events
Submit events
Party Image Gallery
View and download HQ party images
Sign up as a contributing event photographer and get paid!
Tickets
Sell your event tickets online for free!
Direct pay
No ticket fee

Target Market(s)

These cards will be handed out in clubs and events to patrons.

Industry/Entity Type

Business

Contact Information for Business Card

Should match or mirror our website in some sort of way. Visit the website to get ideas.

Requirements
Must have
• Must be designed for a 3x3 inch card.

```html
<!DOCTYPE html>
<html lang="en">
<head>
<meta charset="utf-8">
<title>RevelHubQZ Business Cards</title>
<link href="https://fonts.googleapis.com/css2?family=Mulish:wght@700&family=Questrial&display=swap" rel="stylesheet">
<style>
  :root {
    --stage: #e0e0de;
    --card: #2a2a2a;
    --blue: #00a8e6;
    --pink: #e0337f;
    --white: #ffffff;
    --text-soft: #f2f2f2;
  }
  html, body { margin: 0; padding: 0; overflow: hidden; }
  body {
    width: 1200px; height: 659px;
    background: var(--stage);
    position: relative;
    font-family: "Questrial", sans-serif;
  }
  .card {
    position: absolute; top: 142px;
    width: 374px; height: 374px;
    background: var(--card);
    overflow: hidden;
  }
  .card--front { left: 201px; }
  .card--back { left: 623px; }

  .brand-mark {
    position: absolute; left: 0; right: 0; top: 52px;
    margin: 0 auto; width: 58px; height: 58px;
    border-radius: 50%; background: var(--blue);
  }
  .brand-name {
    position: absolute; left: 0; right: 0; top: 114px;
    text-align: center; font-size: 27px; color: var(--blue);
    letter-spacing: 0.5px;
  }
  .brand-slogan {
    position: absolute; left: 0; right: 0; top: 141px;
    text-align: center; font-size: 8.5px; color: var(--text-soft);
    letter-spacing: 4px;
  }
  .front-wave { position: absolute; left: 0; top: 180px; }
  .contact {
    position: absolute; left: 0; right: 0; top: 222px;
    text-align: center; color: var(--white);
  }
  .contact__name { font-family: "Mulish", sans-serif; font-weight: 700; font-size: 20px; margin: 0; }
  .contact__title { font-size: 12px; margin: 2px 0 16px; }
  .contact__line { font-size: 14px; margin: 0; line-height: 16.5px; }
  .eq-strip {
    position: absolute; left: 0; right: 0; bottom: 0;
  }
  .eq-strip--front { height: 14px; background: linear-gradient(#6fcff3, #d9f3fc); opacity: .9; }
  .eq-strip--back { height: 33px; background: linear-gradient(var(--pink) 0%, var(--pink) 45%, var(--blue) 55%, var(--blue) 100%); }

  .offer-title {
    position: absolute; left: 0; right: 0; top: 44px;
    text-align: center; margin: 0;
    font-family: "Mulish", sans-serif; font-weight: 700;
    font-size: 17px; color: var(--pink);
  }
  .offer-list {
    position: absolute; left: 0; right: 0; top: 79px;
    list-style: none; margin: 0; padding: 0;
    text-align: center; color: var(--text-soft);
    font-size: 14.5px; line-height: 21.6px;
  }
</style>
</head>
<body>
  <section class="card card--front">
    <div class="brand-mark"></div>
    <div class="brand-name">RevelHubQZ</div>
    <div class="brand-slogan">discover the nightlife</div>
    <svg class="front-wave" width="374" height="194" viewBox="0 0 374 194">
      <path d="M0 30 Q187 -14 374 30 L374 194 L0 194 Z" fill="var(--pink)"/>
      <path d="M0 34 Q187 -2 374 34 L374 194 L0 194 Z" fill="var(--blue)"/>
    </svg>
    <div class="contact">
      <p class="contact__name">Dana Whitlock</p>
      <p class="contact__title">Managing Director</p>
      <p class="contact__line">5182297734</p>
      <p class="contact__line">support@revelhubqz-example.net</p>
      <p class="contact__line">www.revelhubqz-example.net</p>
    </div>
    <div class="eq-strip eq-strip--front" role="img" aria-label="Light equalizer bar pattern"></div>
  </section>

  <section class="card card--back">
    <h2 class="offer-title">WE OFFER</h2>
    <ul class="offer-list">
      <li>Events</li>
      <li>Search upcoming events</li>
      <li>Submit events</li>
      <li>Party Image Gallery</li>
      <li>View and download HQ party images</li>
      <li>Sign up as a contributing event</li>
      <li>photographer and get paid!</li>
      <li>Tickets</li>
      <li>Sell your event tickets online for free!</li>
      <li>Direct pay</li>
      <li>No ticket fee</li>
    </ul>
    <div class="eq-strip eq-strip--back" role="img" aria-label="Pink and blue equalizer bar pattern"></div>
  </section>
</body>
</html>
```